Corvane Freight Company Business Card Design

We are a company that delivers natural saltwater (from the ocean) to aquarium companies, restaurants and home marine tanks. I would like a new business card to suit.

Must include Name, company name, abn, contact number and website as well as logo (see attached).

Looking for a design that stands out, has a clean but unique appearance.

Double and single sided entries welcome

Business

• Logo

```html
<!DOCTYPE html>
<html lang="en">
<head>
<meta charset="utf-8">
<title>Corvane Freight Company – Business Card</title>
<link rel="stylesheet" href="https://fonts.googleapis.com/css2?family=Open+Sans:ital,wght@0,400;0,600;0,700;1,700&display=swap">
<style>
  :root {
    --stage: #1b1b1b;
    --card: #ffffff;
    --brand-blue: #1a8fd2;
    --deep-blue: #1f6db5;
    --sky: #5acdf4;
    --ink: #1a1a1a;
    --text-dark: #222222;
  }
  * { margin: 0; padding: 0; box-sizing: border-box; }
  html, body {
    width: 1200px; height: 420px; overflow: hidden;
    background: var(--stage);
    font-family: "Open Sans", Arial, sans-serif;
  }
  .stage { position: relative; width: 1200px; height: 420px; }
  .card {
    position: absolute; top: 66px;
    width: 525px; height: 298px;
    background: var(--card);
    border-radius: 24px;
    overflow: hidden;
  }
  .card--front { left: 69px; }
  .card--back { left: 622px; }

  .wave-band { position: absolute; left: 0; top: 0; width: 525px; height: 298px; }

  .brand-name {
    position: absolute;
    color: var(--brand-blue);
    font-weight: 600;
    white-space: nowrap;
    letter-spacing: -0.3px;
  }
  .card--front .brand-name { left: 30px; top: 118px; font-size: 23px; }
  .card--back .brand-name { left: 0; right: 0; top: 130px; text-align: center; font-size: 38px; }

  .address {
    position: absolute; left: 328px; top: 68px;
    font-size: 12.5px; line-height: 20px; color: var(--text-dark);
  }
  .abn { margin-top: 10px; }

  .holder {
    position: absolute; left: 57px; top: 264px;
    font-size: 16px; color: var(--deep-blue); font-weight: 700;
  }
  .holder .title { font-weight: 400; }

  .contact {
    position: absolute; left: 327px; top: 245px;
    list-style: none; font-size: 12.5px; line-height: 20px; color: var(--deep-blue);
  }
  .contact li { display: flex; align-items: center; gap: 7px; }
  .contact svg { width: 10px; height: 10px; }
</style>
</head>
<body>
<main class="stage">
  <section class="card card--front" aria-label="Business card front">
    <svg class="wave-band" viewBox="0 0 525 298" aria-hidden="true">
      <path d="M0 190 C 80 250, 200 250, 300 225 C 400 200, 470 195, 525 198 L525 205 C 470 203, 400 208, 300 232 C 200 256, 80 255, 0 196 Z" fill="var(--sky)"/>
      <path d="M0 206 C 80 262, 200 262, 300 238 C 400 214, 470 208, 525 210 L525 215 C 470 214, 400 220, 300 243 C 200 267, 80 268, 0 212 Z" fill="var(--ink)"/>
      <path d="M0 214 C 80 272, 200 272, 300 248 C 400 224, 470 218, 525 219 L525 298 L0 298 Z" fill="var(--sky)"/>
    </svg>

    <div class="brand-name">Corvane Freight Company</div>

    <address class="address">
      Street Name, City Name<br>
      State, Zip Code
      <div class="abn">ABN: 123456789</div>
    </address>

    <p class="holder">Your Name, <span class="title">Title</span></p>

    <ul class="contact">
      <li>
        <svg viewBox="0 0 10 10" aria-hidden="true"><circle cx="5" cy="5" r="4.3" fill="none" stroke="currentColor" stroke-width="1"/><path d="M3.4 2.6 L4.3 3.7 L3.8 4.3 C4.2 5.1 4.9 5.8 5.7 6.2 L6.3 5.7 L7.4 6.6 L6.8 7.4 C5 7.2 2.8 5 2.6 3.2 Z" fill="currentColor"/></svg>
        123-456-7892
      </li>
      <li>
        <svg viewBox="0 0 10 10" aria-hidden="true"><g fill="none" stroke="currentColor" stroke-width="0.9"><circle cx="5" cy="5" r="4.3"/><ellipse cx="5" cy="5" rx="1.8" ry="4.3"/><path d="M0.7 5 H9.3 M1.5 2.8 H8.5 M1.5 7.2 H8.5"/></g></svg>
        www.corvanefreight.com
      </li>
    </ul>
  </section>

  <section class="card card--back" aria-label="Business card back">
    <div class="brand-name">Corvane Freight Company</div>
  </section>
</main>
</body>
</html>
```